Local massage therapist needs some new marketing material

Hi there! I am a massage therapist here in Denver, CO in Alder Bend(shopping and art district) of the city. My business is called Lumo Bodywork of Denver. My practice has an eastern influence and I do reflexology, thai massage and use Chinese herbs, etc. I know all my clients and pay close attention to details. I am also very respectful of tradition and it shows in how I work. I tend to like modern, clean, fun, Asian designs. I am wanting a new business card and brochure. I have a logo and branding for my business that I want used in the design. Currently, the sign for my building is purple and I think my logo was designed to be purple. I will attach pictures of it and can send whatever files are necessary so it can be integrated into the brochure, etc. I like the purple but open to using other colors as well. Thanks!
My website is lumobodyworkofdenver.example where info can be gathered about me and services/fees for brochure.
Updates

Just increased budget. Please see new feedback in discussion thread.

Thanks!

                                       HEY ALL,

Just wanted to let you know that I made a change to my website. It is on the Prices Page. I no longer have the frequent  flyer prices but I added discounts. Let me know if you have any questions. Thanks so much!

Target Market(s)

healthy, urban, educated, upper middle class, yogis

Industry/Entity Type

Marketing

Requirements
Must have
• logo stays purple
Should not have
• not too busy

```html
<!DOCTYPE html>
<html lang="en">
<head>
<meta charset="utf-8">
<title>Lumo Bodywork of Denver — Business Card</title>
<link rel="stylesheet" href="https://fonts.googleapis.com/css2?family=Josefin+Sans:wght@300&family=Roboto+Slab:wght@400&display=swap">
<style>
  :root {
    --backdrop: #e9e7ec;
    --card-purple: #6a1b8f;
    --card-purple-deep: #5a1479;
    --ornament-tint: rgba(255, 255, 255, 0.07);
    --ink-light: #ffffff;
    --ink-purple: #6a1b8f;
    --shadow: rgba(40, 20, 50, 0.22);
  }
  * { box-sizing: border-box; margin: 0; padding: 0; }
  html, body { width: 1200px; height: 872px; overflow: hidden; }
  body {
    background: var(--backdrop);
    position: relative;
  }
  .card {
    position: absolute;
    top: 286px;
    width: 525px;
    height: 300px;
    background: var(--card-purple);
    box-shadow: 0 10px 28px var(--shadow);
    overflow: hidden;
  }
  .card--back { left: 45px; }
  .card--front { left: 630px; }

  /* Back side: contact details */
  .social-band {
    position: absolute;
    top: 0; left: 0;
    width: 100%;
    height: 52px;
    background: var(--ink-light);
    display: flex;
    align-items: center;
    gap: 12px;
    padding-left: 36px;
  }
  .social-band .social-dot {
    width: 14px; height: 14px;
    background: var(--ink-purple);
  }
  .contact-list {
    position: absolute;
    top: 72px; left: 36px;
    list-style: none;
    font-family: "Roboto Slab", Georgia, serif;
    font-size: 14.5px;
    line-height: 25px;
    color: var(--ink-light);
  }
  .contact-list .hours { font-style: normal; }
  .ornament {
    position: absolute;
    border-radius: 50%;
    background: radial-gradient(circle, var(--ornament-tint) 0%, rgba(255,255,255,0.04) 55%, rgba(255,255,255,0) 72%);
  }
  .card--back .ornament { width: 260px; height: 260px; right: -70px; bottom: -100px; }

  /* Front side: brand */
  .card--front .ornament { width: 300px; height: 300px; left: -90px; bottom: -130px; }
  .brand {
    position: absolute;
    top: 92px; left: 0; width: 100%;
    display: flex;
    justify-content: center;
    align-items: center;
    gap: 22px;
  }
  .brand-name {
    font-family: "Josefin Sans", Arial, sans-serif;
    font-weight: 300;
    font-size: 58px;
    letter-spacing: 14px;
    color: var(--ink-light);
    line-height: 1;
  }
  .brand-mark {
    width: 46px; height: 46px;
    border: 1.5px solid var(--ink-light);
    border-radius: 50%;
  }
  .website {
    position: absolute;
    top: 178px; left: 0; width: 100%;
    text-align: center;
    font-family: "Roboto Slab", Georgia, serif;
    font-size: 15px;
    letter-spacing: 0.5px;
    color: var(--ink-light);
  }
</style>
</head>
<body>
  <section class="card card--back" aria-label="Card back with contact details">
    <div class="social-band">
      <span class="social-dot"></span>
      <span class="social-dot"></span>
      <span class="social-dot"></span>
    </div>
    <ul class="contact-list">
      <li>1480 E Larch Ave, Denver, CO 80206</li>
      <li>P. 303.555.0148</li>
      <li>+91-0000000000, +91-0000000000</li>
      <li>info@lumobodyworkofdenver.example</li>
      <li>(Appointments required) No walk-ins please</li>
      <li class="hours">Tues - Fri: 10am - 8pm Sat: 10am-5pm</li>
    </ul>
    <div class="ornament" role="img" aria-label="Faint circular floral ornament in lighter purple"></div>
  </section>

  <section class="card card--front" aria-label="Card front with brand name">
    <div class="ornament" role="img" aria-label="Faint circular floral ornament in lighter purple"></div>
    <div class="brand">
      <span class="brand-name">LUMO</span>
      <span class="brand-mark"></span>
    </div>
    <p class="website">www.lumobodyworkofdenver.example</p>
  </section>
</body>
</html>
```